Business Card for Coastal Tundrabridge Advisory

We need a business card for Coastal Tundrabridge Advisory. The company website address is provided below. The company logo is attached. We provide specialized permafrost services to the mining, transportation, and oil & gas industries. The card should be prepared for:
Matthias Korhonen, PhD.
Coastal Tundrabridge Advisory
PO Box 418259
Quillwater, Alaska 99642
Direct: +1-907-555-0143
Email: mkorhonen@tundrabridgeadvisory.example
Website: www.coastaltundrabridgeadvisory.example

```html
<!DOCTYPE html>
<html lang="en">
<head>
<meta charset="utf-8">
<title>Coastal Tundrabridge Advisory – Business Card</title>
<link href="https://fonts.googleapis.com/css2?family=Arimo:wght@400;700&family=Montserrat:wght@600&display=swap" rel="stylesheet">
<style>
  :root {
    --backdrop: #d9d9da;
    --card-light: #f4f4f4;
    --card-dark: #0f1720;
    --stripe: #4a4a4c;
    --ink-light: #ffffff;
  }
  * { margin: 0; padding: 0; box-sizing: border-box; }
  html, body { width: 1200px; height: 1040px; overflow: hidden; }
  body { background: var(--backdrop); font-family: "Arimo", Arial, sans-serif; position: relative; }

  .card {
    position: absolute; left: 285px; width: 645px; height: 367px;
    border-radius: 16px; overflow: hidden;
  }
  .card--front { top: 130px; background: var(--card-light); }
  .card--back { top: 568px; background: var(--card-dark); }

  .front-shape { position: absolute; inset: 0; width: 100%; height: 100%; }

  .wordmark {
    position: absolute; font-family: "Montserrat", sans-serif; font-weight: 600;
    text-transform: uppercase; letter-spacing: 0.08em; line-height: 1.15;
  }
  .card--front .wordmark { left: 35px; top: 64px; font-size: 22px; color: var(--card-dark); }
  .card--back .wordmark {
    left: 0; right: 0; top: 108px; text-align: center;
    font-size: 36px; color: var(--ink-light);
  }

  .contact {
    position: absolute; right: 28px; top: 166px; text-align: right;
    color: var(--ink-light); font-size: 15px; line-height: 20px;
  }
  .contact__address { margin-right: 2px; }
  .contact__lines { margin-top: 11px; }
  .contact__line { display: flex; justify-content: flex-end; align-items: center; gap: 8px; }
  .contact__icon { width: 13px; height: 13px; flex: none; }
  .contact__person { margin-top: 13px; }
  .contact__name { font-size: 22px; font-weight: 700; line-height: 28px; }
  .contact__name small { font-size: 18px; }
  .contact__title { font-size: 15px; }

  .back-web {
    position: absolute; left: 0; right: 0; top: 318px; text-align: center;
    color: var(--ink-light); font-size: 15px;
  }
</style>
</head>
<body>
  <section class="card card--front">
    <svg class="front-shape" viewBox="0 0 645 367" preserveAspectRatio="none" aria-hidden="true">
      <polygon points="459,0 645,0 645,367 201,367" fill="var(--card-dark)"/>
      <polygon points="154,367 177,367 455,2 450,2" fill="var(--stripe)"/>
    </svg>
    <div class="wordmark">Coastal Tundrabridge<br>Advisory</div>
    <div class="contact">
      <div class="contact__address">PO Box 418259<br>Quillwater, Alaska 99642</div>
      <div class="contact__lines">
        <div class="contact__line">+1-907-555-0143
          <svg class="contact__icon" viewBox="0 0 24 24" aria-hidden="true"><path fill="#fff" d="M6.6 10.8a15 15 0 0 0 6.6 6.6l2.2-2.2c.3-.3.7-.4 1-.2 1.1.4 2.3.6 3.6.6.6 0 1 .4 1 1V20c0 .6-.4 1-1 1A17 17 0 0 1 3 4c0-.6.4-1 1-1h3.5c.6 0 1 .4 1 1 0 1.3.2 2.5.6 3.6.1.3 0 .7-.2 1z"/></svg>
        </div>
        <div class="contact__line">mkorhonen@tundrabridgeadvisory.example
          <svg class="contact__icon" viewBox="0 0 24 24" aria-hidden="true"><path fill="#fff" d="M2 5h20v14H2z"/><path fill="none" stroke="#0f1720" stroke-width="2" d="M2 6l10 7 10-7"/></svg>
        </div>
        <div class="contact__line">www.coastaltundrabridgeadvisory.example
          <svg class="contact__icon" viewBox="0 0 24 24" aria-hidden="true"><circle cx="12" cy="12" r="10" fill="#fff"/><path fill="none" stroke="#0f1720" stroke-width="1.6" d="M12 2c-3 3-3 17 0 20M2 12h20M4 7h16M4 17h16"/></svg>
        </div>
      </div>
      <div class="contact__person">
        <div class="contact__name">Matthias Korhonen, <small>PhD.</small></div>
        <div class="contact__title">President</div>
      </div>
    </div>
  </section>

  <section class="card card--back">
    <div class="wordmark">Coastal Tundrabridge<br>Advisory</div>
    <div class="back-web">www.coastaltundrabridgeadvisory.example</div>
  </section>
</body>
</html>
```